Every Shelf Set Neatly or ESN Organized needs a business card design. ESN Organized is a professi

We need a business card design that is clean, sharp and conveys a sense of organization. I already have a logo.

Target Market(s)

Families (specifically mothers), small business owners, parents, seniors

Industry/Entity Type

Business

Contact Information for Business Card

My website is www.esnorganized-example.com and my Facebook page is http://www.sociallink-example.com/everyshelfsetneatly. The phone number is 418-552-7094 and I want to be listed as Lorna M. Pelham, Owner

Requirements
Must have
• My logo.

```html
<!DOCTYPE html>
<html lang="en">
<head>
<meta charset="utf-8">
<title>ESN Organized – Business Card</title>
<link rel="stylesheet" href="https://fonts.googleapis.com/css2?family=Arimo:wght@400;700&family=Montserrat:wght@200;300;400;500&display=swap">
<style>
  :root {
    --page-bg: #e9ebee;
    --card-white: #ffffff;
    --card-shade: #eef0f2;
    --brand-blue: #1f86d9;
    --brand-blue-deep: #0d5aa8;
    --ink-dark: #1c1c1c;
    --ink-grey: #6b6b6b;
    --ink-soft: #9a9a9a;
  }
  * { box-sizing: border-box; margin: 0; padding: 0; }
  html, body { width: 1200px; height: 950px; overflow: hidden; }
  body {
    background: var(--page-bg);
    display: flex;
    flex-direction: column;
    align-items: center;
    justify-content: center;
    gap: 60px;
  }
  .card {
    position: relative;
    width: 700px;
    height: 400px;
    border-radius: 4px;
    box-shadow: 0 10px 30px rgba(0,0,0,0.18);
    overflow: hidden;
  }

  /* Front */
  .card-front {
    background: linear-gradient(160deg, var(--card-white) 55%, var(--card-shade) 100%);
  }
  .identity {
    position: absolute;
    right: 46px;
    top: 62px;
    text-align: right;
    font-family: 'Arimo', Arial, sans-serif;
  }
  .identity .person-name {
    color: var(--brand-blue);
    font-weight: 700;
    font-size: 28px;
    letter-spacing: 0.3px;
  }
  .identity .person-role {
    color: var(--ink-dark);
    font-weight: 700;
    font-size: 19px;
    margin-top: 6px;
  }
  .wordmark {
    position: absolute;
    right: 46px;
    top: 160px;
    display: flex;
    align-items: center;
    gap: 14px;
    font-family: 'Montserrat', sans-serif;
    font-weight: 400;
    font-size: 30px;
    letter-spacing: 3px;
    color: var(--ink-dark);
  }
  .wordmark .mark-dot {
    width: 16px;
    height: 16px;
    border-radius: 50%;
    background: var(--brand-blue);
  }
  .contact-list {
    position: absolute;
    right: 46px;
    bottom: 46px;
    list-style: none;
    font-family: 'Arimo', Arial, sans-serif;
    font-size: 21px;
    color: var(--ink-grey);
  }
  .contact-list li {
    display: flex;
    align-items: center;
    justify-content: flex-end;
    gap: 14px;
    height: 34px;
  }
  .contact-list svg { width: 22px; height: 22px; flex: none; }
  .icon-fill { fill: var(--brand-blue); }

  /* Back */
  .card-back {
    background: linear-gradient(135deg, var(--brand-blue) 0%, #1a73c4 55%, var(--brand-blue-deep) 100%);
    display: flex;
    flex-direction: column;
    align-items: center;
    justify-content: center;
    color: var(--card-white);
  }
  .back-name {
    font-family: 'Montserrat', sans-serif;
    font-weight: 200;
    font-size: 150px;
    letter-spacing: 12px;
    line-height: 1;
  }
  .back-url {
    font-family: 'Montserrat', sans-serif;
    font-weight: 300;
    font-size: 20px;
    letter-spacing: 6px;
    margin-top: 18px;
    opacity: 0.85;
  }
</style>
</head>
<body>

  <section class="card card-front" aria-label="Business card front">
    <div class="identity">
      <p class="person-name">Lorna M. Pelham</p>
      <p class="person-role">Owner</p>
    </div>

    <div class="wordmark">
      <span class="mark-dot"></span>
      <span class="wordmark-text">ESN Organized</span>
    </div>

    <ul class="contact-list">
      <li>
        <span>418-552-7094</span>
        <svg viewBox="0 0 24 24" aria-hidden="true">
          <path class="icon-fill" d="M6.6 10.8a15.1 15.1 0 0 0 6.6 6.6l2.2-2.2a1 1 0 0 1 1-.25 11.4 11.4 0 0 0 3.6.57 1 1 0 0 1 1 1V20a1 1 0 0 1-1 1A17 17 0 0 1 3 4a1 1 0 0 1 1-1h3.5a1 1 0 0 1 1 1c0 1.25.2 2.45.57 3.57a1 1 0 0 1-.25 1z"/>
        </svg>
      </li>
      <li>
        <span>www.esnorganized-example.com</span>
        <svg viewBox="0 0 24 24" aria-hidden="true">
          <circle cx="12" cy="12" r="10" fill="none" stroke="var(--brand-blue)" stroke-width="2"/>
          <ellipse cx="12" cy="12" rx="4.5" ry="10" fill="none" stroke="var(--brand-blue)" stroke-width="1.6"/>
          <line x1="2" y1="12" x2="22" y2="12" stroke="var(--brand-blue)" stroke-width="1.6"/>
        </svg>
      </li>
      <li>
        <span>everyshelfsetneatly</span>
        <svg viewBox="0 0 24 24" aria-hidden="true">
          <rect class="icon-fill" x="2" y="2" width="20" height="20" rx="2"/>
        </svg>
      </li>
    </ul>
  </section>

  <section class="card card-back" aria-label="Business card back">
    <p class="back-name">ESN</p>
    <p class="back-url">esnorganized-example.com</p>
  </section>

</body>
</html>
```